Looking for a dynamic business card for a pizzeria.

A business card with our food, logo, and space for name, title, email, website, phone. The card should convey quality, unique, amazing. On the front, I envision food photo or photos with the owners names and contact information. On the back, more food with locations, website, facebook, twitter, instagram icons. It should look polished, not cartoonish, or plain.
Target Market(s)
upscale, local food buyers, 30-50 years in age.
Industry/Entity Type
Restaurant
Contact Information for Business Card
Business Name: Bru'nettix, LLC
Website: www.brunettix.com
Back:
2 locations: (can list on the back of card)
1. Corlan Point
4087 Corlan Avenue
Ardenvale, OR 97814
360-481-5067
2. Wendmere Hill
7315 Wendmere Road
Ardenvale, OR 97816
360-293-8840
front:
EDITABLE space for
Business name
Person's Name
title
2nd title
Email address
cell-phone number
Requirements
Must have
- logo
- my food photo or photos (no watermarks showing)
- locations on back
- Person contact information on front
- full bleed

```html
<!DOCTYPE html>
<html lang="en">
<head>
<meta charset="utf-8">
<title>Bru'nettix Business Card</title>
<link href="https://fonts.googleapis.com/css2?family=Arimo:wght@400;700&display=swap" rel="stylesheet">
<style>
  :root {
    --bg: #ecebe7;
    --red: #c0160f;
    --green: #1f5a2a;
    --white: #ffffff;
    --ink-light: #ffffff;
    --photo-a: #c89a5a;
    --photo-b: #7d5a2e;
    --photo-c: #5f7d3a;
    --shadow: 0 14px 30px rgba(0,0,0,0.22);
  }
  * { box-sizing: border-box; margin: 0; padding: 0; }
  html, body { width: 1200px; height: 950px; overflow: hidden; }
  body {
    background: var(--bg);
    font-family: "Arimo", Arial, sans-serif;
    display: flex;
    flex-direction: column;
    align-items: center;
    justify-content: center;
    gap: 50px;
  }
  .card {
    position: relative;
    width: 700px;
    height: 400px;
    overflow: hidden;
    box-shadow: var(--shadow);
    background: var(--white);
  }

  /* Back side */
  .card-back .food-photo {
    position: absolute;
    inset: 0 0 148px 0;
    background: linear-gradient(135deg, var(--photo-a) 0%, var(--photo-b) 45%, var(--photo-c) 70%, var(--photo-a) 100%);
  }
  .card-back .social-icons {
    position: absolute;
    top: 16px;
    right: 20px;
    display: flex;
    gap: 10px;
  }
  .card-back .location-band {
    position: absolute;
    left: 0; right: 0; bottom: 0;
    height: 148px;
    background: var(--red);
    color: var(--ink-light);
    display: flex;
    justify-content: space-between;
    padding: 22px 30px;
    font-size: 17px;
    line-height: 1.3;
  }
  .location { font-style: normal; }
  .location.left { align-self: flex-end; }
  .location.right { align-self: flex-start; text-align: right; }
  .location .location-name { font-weight: 700; }
  .location .label { font-weight: 700; }

  /* Front side */
  .card-front .brand {
    position: absolute;
    top: 100px;
    left: 150px;
    display: flex;
    align-items: center;
    gap: 14px;
  }
  .brand-name {
    font-size: 54px;
    font-weight: 700;
    color: var(--green);
    letter-spacing: 1px;
  }
  .brand-mark {
    width: 56px; height: 56px;
    border-radius: 50%;
    background: var(--red);
  }
  .card-front .contact-band {
    position: absolute;
    left: 0; right: 0; bottom: 0;
    height: 170px;
    background: var(--green);
    color: var(--ink-light);
  }
  .contact-list {
    position: absolute;
    top: 22px;
    right: 26px;
    list-style: none;
    text-align: right;
    font-size: 17px;
    line-height: 1.55;
  }
  .contact-list li { display: flex; align-items: center; justify-content: flex-end; gap: 10px; }
  .contact-list svg { width: 16px; height: 16px; fill: var(--white); }
  .person {
    position: absolute;
    left: 30px;
    bottom: 26px;
  }
  .person-name { font-size: 24px; font-weight: 700; letter-spacing: 0.5px; }
  .person-title { font-size: 17px; margin-top: 4px; }
</style>
</head>
<body>

<section class="card card-back">
  <div class="food-photo" role="img" aria-label="Close-up photo of a toasted grilled sandwich with greens, ham and tomato"></div>
  <div class="social-icons">
    <svg width="18" height="18" viewBox="0 0 18 18"><circle cx="9" cy="9" r="8" fill="#ffffff"/></svg>
    <svg width="18" height="18" viewBox="0 0 18 18"><circle cx="9" cy="9" r="8" fill="#ffffff"/></svg>
  </div>
  <div class="location-band">
    <address class="location left">
      <div class="location-name">Corlan Point</div>
      <div>4087 Corlan Avenue,</div>
      <div>Ardenvale, OR 97814</div>
      <div><span class="label">Phone:</span> 360-481-5067</div>
    </address>
    <address class="location right">
      <div class="location-name">Wendmere Hill</div>
      <div>7315 Wendmere Road</div>
      <div>Ardenvale, OR 97816</div>
      <div><span class="label">Phone:</span>360-293-8840</div>
    </address>
  </div>
</section>

<section class="card card-front">
  <div class="brand">
    <span class="brand-name">BRU'NETTIX</span>
    <span class="brand-mark"></span>
  </div>
  <div class="contact-band">
    <ul class="contact-list">
      <li>689 502 7194
        <svg viewBox="0 0 16 16"><rect x="4" y="1" width="8" height="14" rx="1.5"/><rect x="5.5" y="3" width="5" height="8" fill="#1f5a2a"/></svg>
      </li>
      <li>name@brunettix.com
        <svg viewBox="0 0 16 16"><rect x="1" y="3" width="14" height="10" rx="1"/><path d="M1.5 3.5 L8 9 L14.5 3.5" stroke="#1f5a2a" stroke-width="1.4" fill="none"/></svg>
      </li>
      <li>www.brunettix.com
        <svg viewBox="0 0 16 16"><circle cx="8" cy="8" r="7"/><circle cx="8" cy="8" r="3" fill="#1f5a2a"/></svg>
      </li>
    </ul>
    <div class="person">
      <div class="person-name">ELLIS VARNE</div>
      <div class="person-title">President</div>
    </div>
  </div>
</section>

</body>
</html>
```